The Brandwell Firm

We need a new design for our letterhead and envelopes. We are a personal injury and criminal defense firm so we need something modern and clean, but more on the professional/traditional side. Our new logo has two colors and is attached to the file so we need something that works well with those colors/matches the design. The following information needs to be on the letterhead:
Phone: (555) 214-3370
Fax: (555) 214-5186
Toll-Free: (888) 431-2059
Post Office Box 4721
Millbrook, SC 29555-4721
HarmClaimCounsel.example
PalmettoTrialAdvocates.example

Target Market(s)

Clients, government agencies, other law firms

Industry/Entity Type

Legal

Font styles to use
Sans Serif
Other font styles liked:
• Arial

Colors

Designer to choose colors to be used in the design.

Requirements
Must have
• Must look professional and clean, modern
Nice to have
• I would like to see a design that works with the logo but does not distract from the content that will be printed on it
Should not have
• Too many colors or crazy designs.

```html
<!DOCTYPE html>
<html lang="en">
<head>
<meta charset="utf-8">
<title>The Brandwell Firm — Letterhead and Envelope</title>
<link rel="stylesheet" href="https://fonts.googleapis.com/css2?family=Open+Sans:wght@400;600&display=swap">
<style>
  :root {
    --backdrop: #5b5d60;
    --paper: #fdfdfd;
    --ink: #333338;
    --brand-red: #d0232a;
    --brand-blue: #2e3192;
    --white: #ffffff;
  }
  * { box-sizing: border-box; margin: 0; padding: 0; }
  html, body { width: 1200px; height: 904px; overflow: hidden; }
  body {
    background: var(--backdrop);
    font-family: "Open Sans", Arial, sans-serif;
    color: var(--ink);
    position: relative;
  }
  .sheet {
    position: absolute;
    background: var(--paper);
    box-shadow: 0 2px 8px rgba(0,0,0,.35);
  }
  .letterhead { left: 82px; top: 114px; width: 492px; height: 695px; }
  .envelope-front { left: 604px; top: 254px; width: 509px; height: 253px; }
  .envelope-back { left: 604px; top: 545px; width: 509px; height: 254px; }

  .brand {
    position: absolute;
    display: flex;
    align-items: center;
    gap: 6px;
    font-weight: 600;
    color: var(--brand-red);
    line-height: 1.05;
    letter-spacing: .04em;
    text-transform: uppercase;
  }
  .brand-dot { width: 10px; height: 10px; border-radius: 50%; background: var(--brand-blue); flex: none; }
  .brand-name { font-size: 16px; }
  .letterhead .brand { left: 31px; top: 162px; top: 36px; }
  .envelope-front .brand { left: 30px; top: 30px; }
  .envelope-back .brand {
    left: 50%; top: 22px; transform: translateX(-50%);
    color: var(--white);
  }
  .envelope-back .brand-name { font-size: 13px; }
  .envelope-back .brand-dot { background: var(--white); width: 8px; height: 8px; }

  .return-address {
    position: absolute; left: 40px; top: 81px; width: 110px;
    font-size: 7.5px; line-height: 11px; text-align: center;
  }

  .contact {
    position: absolute;
    text-align: right;
    font-size: 7.5px;
    line-height: 13px;
    white-space: nowrap;
  }
  .letterhead .contact { right: 45px; top: 654px; }
  .envelope-front .contact { right: 44px; top: 209px; }
  .contact svg { width: 7px; height: 7px; vertical-align: -1px; margin-right: 2px; fill: var(--brand-blue); }

  .accent-bars { position: absolute; display: flex; gap: 1px; height: 26px; }
  .accent-bars span { width: 2px; height: 100%; }
  .accent-bars .bar-blue { background: var(--brand-blue); }
  .accent-bars .bar-red { background: var(--brand-red); }
  .letterhead .accent-bars { left: 463px; top: 654px; }
  .envelope-front .accent-bars { left: 477px; top: 210px; height: 24px; }

  .flap { position: absolute; left: 0; top: 0; width: 509px; height: 74px; }
</style>
</head>
<body>

  <section class="sheet letterhead" aria-label="Letterhead">
    <div class="brand"><span class="brand-dot"></span><span class="brand-name">The Brandwell Firm</span></div>
    <div class="contact">
      <div>Post Office Box 4721, Millbrook, SC 29555-4721 |
        <svg viewBox="0 0 10 10"><path d="M2 1l2 0 1 2-1 1a5 5 0 0 0 2 2l1-1 2 1v2l-1 1C4 9 1 6 1 2z"/></svg>(555) 214-3370 |
        <svg viewBox="0 0 10 10"><path d="M3 1h4v2H3zM1 4h8v4H7v1H3V8H1z"/></svg>(555) 214-5186 |
        <svg viewBox="0 0 10 10"><path d="M2 1l2 0 1 2-1 1a5 5 0 0 0 2 2l1-1 2 1v2l-1 1C4 9 1 6 1 2z"/></svg> (888) 431-2059</div>
      <div><svg viewBox="0 0 10 10"><circle cx="5" cy="5" r="4.5"/></svg>HarmClaimCounsel.example | PalmettoTrialAdvocates.example</div>
    </div>
    <div class="accent-bars"><span class="bar-blue"></span><span class="bar-red"></span></div>
  </section>

  <section class="sheet envelope-front" aria-label="Envelope front">
    <div class="brand"><span class="brand-dot"></span><span class="brand-name">The Brandwell Firm</span></div>
    <div class="return-address">Post Office Box 4721<br>Millbrook, SC 29555-4721</div>
    <div class="contact">
      <div>Post Office Box 4721, Millbrook, SC 29555-4721 |
        <svg viewBox="0 0 10 10"><path d="M2 1l2 0 1 2-1 1a5 5 0 0 0 2 2l1-1 2 1v2l-1 1C4 9 1 6 1 2z"/></svg>(555) 214-3370 |
        <svg viewBox="0 0 10 10"><path d="M3 1h4v2H3zM1 4h8v4H7v1H3V8H1z"/></svg>(555) 214-5186 |
        <svg viewBox="0 0 10 10"><path d="M2 1l2 0 1 2-1 1a5 5 0 0 0 2 2l1-1 2 1v2l-1 1C4 9 1 6 1 2z"/></svg> (888) 431-2059</div>
      <div><svg viewBox="0 0 10 10"><circle cx="5" cy="5" r="4.5"/></svg>HarmClaimCounsel.example | PalmettoTrialAdvocates.example</div>
    </div>
    <div class="accent-bars"><span class="bar-blue"></span><span class="bar-red"></span></div>
  </section>

  <section class="sheet envelope-back" aria-label="Envelope back">
    <svg class="flap" viewBox="0 0 509 74" aria-hidden="true">
      <path d="M0 0H509C505 22 490 32 470 35L272 69Q254 73 236 69L39 35C19 32 4 22 0 0Z" fill="var(--brand-blue)"/>
    </svg>
    <div class="brand"><span class="brand-dot"></span><span class="brand-name">The Brandwell Firm</span></div>
  </section>

</body>
</html>
```